Web site for small printshop

I am looking for a website for small printshop in Iceland, mainly serving university students and artist.

We print posters, flyers, business cards and more.

In addition to our current website, I would like to include design tool, (fx. www.quarvelpad.example, www.trindomap.example or something similar) jobs upload, shopping chart.
Updates

Great work, I am really amazed of the quality of work i am seeing here.

Really way beyond my expectation

GOOD JOB - all of you ! 

Hi all.

The designs submitted have been great, way better than expected.
I really did not expect this level of quality.

Some have been asking me for feedback on their designs, and I will try 
to send some feedback here, without spoiling your creativity.

Likes:
- when the colors of my logo is used in menus, buttons etc.
- simple, not to crowded look.

Dislikes.
- Dark and heavy design
- Lot of text and buttons (crowded look)

Extra info.
- top line (before menus) will contain: Tel - email - language
- menu line will have 5 categories: Home - service - submission of works - FAQ - about us
- 3 large buttons:  Job submit - Job design - ask for offer

LOVE YOUR WORK - great designs so far :)

Target Market(s)

University Students, Artists. Age group 20-30

Industry/Entity Type

University

Requirements
Must have
• The website must be easy to use, clean looking.

```html
<!DOCTYPE html>
<html lang="en">
<head>
<meta charset="utf-8">
<title>Brautaprent</title>
<link href="https://fonts.googleapis.com/css2?family=Source+Sans+3:wght@400;600;700&display=swap" rel="stylesheet">
<style>
:root{
  --yellow:#f5c400;
  --green:#0d6a3a;
  --red:#e2382c;
  --ink:#1e1e1e;
  --text:#555;
  --rule:#dcdcdc;
  --band:#efefef;
  --footer:#3b3b3b;
  --footer-head:#f2a51a;
  --footer-text:#e6e6e6;
  --hero:#000;
}
*{margin:0;padding:0;box-sizing:border-box}
html,body{width:723px;height:1200px;overflow:hidden;background:#fff}
body{position:relative;font-family:"Source Sans 3",sans-serif;color:var(--text)}
.abs{position:absolute}

/* header */
.brand{left:120px;top:27px;display:flex;align-items:center;gap:6px}
.brand-mark{width:18px;height:18px;background:var(--yellow)}
.brand-name{font-weight:700;font-size:16px;color:var(--ink);letter-spacing:.3px}
.main-nav{right:118px;top:34px;display:flex;gap:8px;font-size:7.2px;font-weight:600;color:var(--ink)}

/* hero */
.hero{left:0;top:65px;width:723px;height:270px;background:var(--hero)}
.hero-collage{left:0;top:0;width:472px;height:270px;background:linear-gradient(120deg,#8a4a2a 0%,#3f6f9f 30%,#7fa9cf 55%,#d0dbe6 75%,#111 100%)}
.hero-side{left:472px;top:0;width:251px;height:270px;text-align:center;color:#fff}
.hero-label{position:absolute;left:0;width:190px;font-size:9.5px;font-weight:600;text-transform:uppercase}
.hero-thumb{position:absolute}
.slider-dots{left:345px;top:246px;display:flex;gap:2px}
.slider-dots span{width:6px;height:6px;border-radius:50%;background:#ddd}
.slider-dots span:first-child{background:#fff;box-shadow:inset 0 0 0 1.5px #555}

/* welcome */
.welcome-title{left:0;width:723px;top:362px;text-align:center;font-size:12px;color:var(--ink)}
.welcome-text{left:118px;width:487px;top:388px;font-size:6.8px;line-height:12.4px;text-align:justify;text-align-last:center}
.rule{left:118px;width:487px;top:450px;height:1px;background:var(--rule)}

/* steps */
.step{width:155px;top:464px;text-align:center}
.step-num{width:28px;height:28px;border-radius:50%;margin:0 auto;color:#fff;font-weight:700;font-size:16px;line-height:28px}
.step-label{font-size:6.5px;font-weight:700;color:var(--ink);margin-top:7px}
.step-title{font-size:9.5px;font-weight:600;color:var(--ink);margin-top:10px}
.step-icon{margin:13px auto 0;display:block}
.step-text{font-size:6.6px;line-height:12.4px;text-align:justify;margin-top:9px}

/* partners */
.partners{left:0;top:664px;width:723px;height:58px;background:var(--band)}
.partner{position:absolute;top:22px;height:14px;border-radius:3px;background:#c9c9c9}

/* features */
.features-title{left:119px;top:746px;font-size:12px;color:var(--ink)}
.feature{width:155px}
.feature h3{font-size:6.8px;font-weight:700;color:var(--ink);margin-bottom:14px}
.feature p{font-size:6.6px;line-height:12.4px;text-align:justify}

/* footer */
.site-footer{left:0;top:1025px;width:723px;height:175px;background:var(--footer);color:var(--footer-text)}
.foot-head{position:absolute;top:18px;font-size:6.5px;color:var(--footer-head);text-transform:uppercase}
.foot-list{position:absolute;top:39px;list-style:none;font-size:6.8px;line-height:12.4px}
.about-photo{position:absolute;left:118px;top:41px;width:114px;height:46px;background:linear-gradient(180deg,#9fb3c2,#5c6670)}
.about-text{position:absolute;left:118px;top:95px;width:114px;font-size:7.2px;line-height:12.4px;text-align:justify}
.news-text{position:absolute;left:408px;top:38px;width:108px;font-size:6.8px;line-height:11px;text-align:justify}
.field{position:absolute;left:408px;width:114px;height:14px;background:#fff;font-size:5px;color:#aaa;padding:4px 2px}
.subscribe{position:absolute;left:472px;top:1109px;}
.btn-subscribe{position:absolute;left:472px;top:109px;width:50px;height:11px;border-radius:6px;background:var(--yellow);color:var(--ink);font-size:6px;font-weight:600;text-align:center;line-height:11px}
.social{position:absolute;left:531px;width:66px;display:flex;justify-content:space-between;align-items:center;font-size:6.8px}
.social i{width:14px;height:14px;border-radius:50%;background:#fff;display:block}
.copyright{position:absolute;left:0;width:723px;top:150px;text-align:center;font-size:6.5px}
</style>
</head>
<body>

<header>
  <div class="abs brand"><span class="brand-mark"></span><span class="brand-name">BRAUTAPRENT</span></div>
  <nav class="abs main-nav"><span>HOME</span><span>ABOUT US</span><span>SERVICES</span><span>SUBMISSION OF WORKS</span><span>UNIVERSITY PRINTING</span></nav>
</header>

<section class="abs hero">
  <div class="abs hero-collage" role="img" aria-label="Hand holding a cascade of floating photo tiles showing printed products"></div>
  <div class="abs hero-side">
    <div class="hero-label" style="top:15px;left:30px">Posters</div>
    <div class="hero-thumb" role="img" aria-label="Three sample posters" style="left:17px;top:39px;width:100px;height:46px;background:linear-gradient(90deg,#1f8fb5,#e8eef2,#2a7fa8)"></div>
    <div class="hero-label" style="top:116px;left:32px">Flyers</div>
    <div class="hero-thumb" role="img" aria-label="Sample event flyer" style="left:37px;top:130px;width:60px;height:57px;background:linear-gradient(180deg,#5a3fa0,#2a1e6a)"></div>
    <div class="hero-label" style="top:207px;left:31px">Business Card</div>
    <div class="hero-thumb" role="img" aria-label="Stack of sample business cards" style="left:20px;top:224px;width:100px;height:32px;background:linear-gradient(100deg,#3a2a1a,#8a6a4a,#e8dcc8)"></div>
  </div>
  <div class="abs slider-dots"><span></span><span></span><span></span><span></span></div>
</section>

<section>
  <h1 class="abs welcome-title" style="font-weight:400">Welcome to Brautaprent</h1>
  <p class="abs welcome-text">Lorem Ipsum is simply dummy text of the printing and typesetting industry. Lorem Ipsum has been the industry's standard dummy text ever since the 1500s, when an unknown printer took a galley of type and scrambled it to make a type specimen book. It has survived not only five centuries, but also the leap into electronic typesetting, remaining essentially unchanged. It was popularised in the 1960s with the release of Letterform sheets containing Lorem Ipsum passages, and more recently with desktop publishing software like Pagewright Desktop including versions of Lorem Ipsum.</p>
  <div class="abs rule"></div>
</section>

<section>
  <div class="abs step" style="left:118px">
    <div class="step-num" style="background:var(--yellow)">1</div>
    <div class="step-label">STEP</div>
    <div class="step-title">Create</div>
    <svg class="step-icon" width="44" height="44" viewBox="0 0 44 44">
      <g fill="#333">
        <rect x="-4" y="18" width="52" height="9" transform="rotate(45 22 22)"/>
        <rect x="-4" y="18" width="52" height="9" transform="rotate(-45 22 22)"/>
      </g>
      <g stroke="#fff" stroke-width="1">
        <line x1="10" y1="14" x2="13" y2="11"/><line x1="16" y1="20" x2="19" y2="17"/><line x1="26" y1="30" x2="29" y2="27"/><line x1="31" y1="35" x2="34" y2="32"/>
      </g>
    </svg>
    <p class="step-text">Lorem Ipsum is simply dummy text of the printing and typesetting industry. Lorem Ipsum has been the industry's standard dummy text ever since the 1500s, when an unknown printer took a galley</p>
  </div>
  <div class="abs step" style="left:284px">
    <div class="step-num" style="background:var(--green)">2</div>
    <div class="step-label">STEP</div>
    <div class="step-title">Upload</div>
    <svg class="step-icon" width="52" height="44" viewBox="0 0 52 44">
      <path d="M10 10h32l9 16v14H1V26z" fill="#333"/>
      <path d="M6 26h12v5h16v-5h12" fill="none" stroke="#fff" stroke-width="2"/>
      <path d="M26 6l-7 8h4v8h6v-8h4z" fill="#fff"/>
    </svg>
    <p class="step-text">Lorem Ipsum is simply dummy text of the printing and typesetting industry. Lorem Ipsum has been the industry's standard dummy text ever since the 1500s, when an unknown printer took a galley</p>
  </div>
  <div class="abs step" style="left:450px">
    <div class="step-num" style="background:var(--red)">3</div>
    <div class="step-label">STEP</div>
    <div class="step-title">Get Printed</div>
    <svg class="step-icon" width="48" height="54" viewBox="0 0 48 54" style="margin-top:8px">
      <rect x="10" y="0" width="28" height="14" fill="#333"/>
      <rect x="0" y="16" width="48" height="22" rx="3" fill="#333"/>
      <rect x="8" y="30" width="32" height="24" fill="#333" stroke="#fff" stroke-width="2"/>
      <g stroke="#fff" stroke-width="1.5"><line x1="13" y1="38" x2="35" y2="38"/><line x1="13" y1="43" x2="35" y2="43"/><line x1="13" y1="48" x2="35" y2="48"/></g>
    </svg>
    <p class="step-text">Lorem Ipsum is simply dummy text of the printing and typesetting industry. Lorem Ipsum has been the industry's standard dummy text ever since the 1500s, when an unknown printer took a galley .</p>
  </div>
</section>

<section class="abs partners" aria-label="Partners">
  <div class="partner" style="left:130px;width:62px"></div>
  <div class="partner" style="left:198px;width:56px"></div>
  <div class="partner" style="left:265px;width:55px"></div>
  <div class="partner" style="left:334px;width:24px"></div>
  <div class="partner" style="left:380px;width:60px"></div>
  <div class="partner" style="left:454px;width:66px"></div>
  <div class="partner" style="left:530px;width:66px"></div>
</section>

<section>
  <h2 class="abs features-title" style="font-weight:400">Our Features</h2>
  <div class="abs feature" style="left:118px;top:779px"><h3>Customizable for a variety of printed products</h3><p>Customizable for any type of printed product - single or double sided, multi-page, with or without layers support; be it business cards, brochures, greeting cards, postcards, stickers, posters, coasters, calendars, T-shirts, mugs, branded business gifts... if you can think of it - we can customize it for you.</p></div>
  <div class="abs feature" style="left:284px;top:779px"><h3>Element-based design</h3><p>Customizable for any type of printed product - single or double sided, multi-page, with or without layers support; be it business cards, brochures, greeting cards, postcards, stickers, posters, coasters, calendars, T-shirts, mugs, branded business gifts... if you can think of it - we can customize it for you.</p></div>
  <div class="abs feature" style="left:450px;top:779px"><h3>Vector / Bitmap elements support</h3><p>Customizable for any type of printed product - single or double sided, multi-page, with or without layers support; be it business cards, brochures, greeting cards, postcards, stickers, posters, coasters, calendars, T-shirts, mugs, branded business gifts... if you can think of it - we can customize it for you.</p></div>
  <div class="abs feature" style="left:118px;top:903px"><h3>Customizable user interface</h3><p>Custom interface - On your request we can build a custom user interface that will both visually and functionally meet your needs - from the simplest product configurator to a full-scale online graphic application.</p></div>
  <div class="abs feature" style="left:284px;top:903px"><h3>Design element libraries</h3><p>Custom interface - On your request we can build a custom user interface that will both visually and functionally meet your needs - from the simplest product configurator to a full-scale online graphic application.</p></div>
  <div class="abs feature" style="left:450px;top:903px"><h3>User interface</h3><p>Custom interface - On your request we can build a custom user interface that will both visually and functionally meet your needs - from the simplest product configurator to a full-scale online graphic application.</p></div>
</section>

<footer class="abs site-footer">
  <div class="foot-head" style="left:118px">About Us</div>
  <div class="foot-head" style="left:242px">Quick Links</div>
  <div class="foot-head" style="left:325px">Support Links</div>
  <div class="foot-head" style="left:408px">Newsletter Signup</div>
  <div class="foot-head" style="left:531px">Connect With Us</div>

  <div class="about-photo" role="img" aria-label="Shop front of the print house"></div>
  <p class="about-text">Lorem Ipsum is simply dummy text of the printing and typesetting industry. Lorem Ipsum has been ...</p>

  <ul class="foot-list" style="left:242px"><li>Home</li><li>About us</li><li>Services</li><li>Submission of works</li><li>University printing</li></ul>
  <ul class="foot-list" style="left:325px;top:40px"><li>Legal Notice</li><li>Privacy Policy</li><li>Terms &amp; Conditions</li><li>Help</li></ul>

  <p class="news-text">Sign-up for our daily emails by entering your information below:</p>
  <div class="field" style="top:68px">Name</div>
  <div class="field" style="top:89px">Enter Your E-Mail ID</div>
  <div class="btn-subscribe">Subscribe</div>

  <div class="social" style="top:36px"><i></i><span>Chirply</span></div>
  <div class="social" style="top:55px"><i></i><span>Pagebook</span></div>
  <div class="social" style="top:74px"><i></i><span>Linkwork</span></div>

  <div class="copyright">© Copyright 2013 .All rights Reserved</div>
</footer>

</body>
</html>
```